Mortgage Company ready to make a statement!

We have a basic logo that I am fairly happy with ... but it could use a little bit of tweaking before we order the sign for our building. We also want some knock-your-socks-off business cards.
Problem: Inside of our Mortgage Office (Bright Fern Mortgage Group), we are going to have a coffee lounge (Sunbrew Cafe) for Realtors to use instead of the local Cuppington to meet with homebuyers. The office and coffee lounge are in an industrial building and is decorated with cozy overstuffed chairs, a hodge podge of interesting lamps and furniture, and goal is to make it as inviting as possible. However, we are a financial institution... so we need to keep it pretty clean as well.
One of my favorite marketing ideas is to cut a house key for everyone who buys a home using us with a key that matches our logo. There's only one key shape that works really well, so that needs to match the logo in order for the idea to work. I'll attach an image of the key blank.... although the way the key hole cut out looks terrible, so I was thinking of having them just do a thin outline instead.
Would like a similar, matching logo for the Sunbrew Cafe... but possibly something that would be a little less formal and would be cute on a coffee mug- nothing stuffy.
AND, we're opening a home inspection company as well, and we would like that logo and branding to match. The home inspection company is "Bright Fern Home Inspections"
We were thinking that for the home inspection company , we could use a magnifying glass shape inside of the house shape for the logo, use a keyhole shape inside of the same house for the mortgage company, and use a coffee cup inside of the house shape for Sunbrew Cafe.
Just getting stuck and need to help. I designed the attached logo myself, and that is what we are currently using. Designers at local printing companies have failed to impress us.
The mortgage industry has a lot of numbers and logos, etc that they require us to put on our business cards... so it's hard to keep them looking clean.
HELP! HELP! :)

```html
<!DOCTYPE html>
<html lang="en">
<head>
<meta charset="UTF-8">
<title>Bright Fern Mortgage Group – Business Card</title>
<link href="https://fonts.googleapis.com/css2?family=Marcellus&family=Work+Sans:wght@400;600&display=swap" rel="stylesheet">
<style>
  :root {
    --brand-blue: #246685;
    --brand-blue-dark: #1f5b79;
    --ink-grey: #555659;
    --text-grey: #4a4a4d;
    --card-white: #ffffff;
    --backdrop: #ecebe8;
  }
  html, body {
    margin: 0;
    padding: 0;
    width: 1200px;
    height: 1000px;
    overflow: hidden;
    background: var(--backdrop);
  }
  .canvas {
    position: relative;
    width: 1200px;
    height: 1000px;
  }
  .card {
    position: absolute;
    left: 275px;
    width: 626px;
    height: 358px;
    box-shadow: 0 4px 14px rgba(0,0,0,0.18);
    overflow: hidden;
  }
  .card-front { top: 133px; background: var(--card-white); }
  .card-back  { top: 507px; background: var(--brand-blue); }

  .brand-name {
    position: absolute;
    font-family: "Marcellus", serif;
    font-weight: 400;
    letter-spacing: 0.5px;
    line-height: 1.05;
    white-space: nowrap;
  }
  .card-front .brand-name {
    right: 46px;
    top: 58px;
    text-align: right;
    font-size: 34px;
    color: var(--brand-blue-dark);
  }
  .card-back .brand-name {
    left: 0;
    right: 0;
    top: 122px;
    text-align: center;
    font-size: 46px;
    color: var(--card-white);
  }
  .brand-name .brand-sub { font-size: 0.68em; }

  .side-tab {
    position: absolute;
    left: 0;
    top: 190px;
    width: 7px;
    height: 47px;
    background: var(--brand-blue);
    border-radius: 0 6px 6px 0;
  }
  .person-name {
    position: absolute;
    left: 45px;
    top: 186px;
    margin: 0;
    font-family: "Marcellus", serif;
    font-size: 25px;
    font-weight: 400;
    letter-spacing: 1px;
    line-height: 32px;
    color: var(--brand-blue-dark);
    white-space: nowrap;
  }
  .person-role {
    position: absolute;
    left: 45px;
    top: 218px;
    font-family: "Work Sans", sans-serif;
    font-weight: 600;
    font-size: 16px;
    line-height: 20px;
    color: var(--text-grey);
  }
  .role-rule {
    position: absolute;
    left: 100px;
    right: 46px;
    top: 229px;
    height: 2px;
    background: var(--brand-blue-dark);
  }
  .contact-list {
    position: absolute;
    left: 45px;
    top: 256px;
    margin: 0;
    padding: 0;
    list-style: none;
    font-family: "Work Sans", sans-serif;
    font-size: 14px;
    letter-spacing: 0.4px;
    color: var(--text-grey);
    white-space: nowrap;
  }
  .contact-list li {
    display: flex;
    align-items: center;
    height: 20px;
  }
  .contact-list svg {
    width: 10px;
    height: 10px;
    margin-right: 12px;
    fill: var(--brand-blue-dark);
  }
  .office-address {
    position: absolute;
    right: 46px;
    top: 279px;
    text-align: right;
    font-family: "Work Sans", sans-serif;
    font-style: normal;
    font-size: 14px;
    letter-spacing: 0.6px;
    line-height: 16px;
    color: var(--text-grey);
    white-space: nowrap;
  }
  .footer-band {
    position: absolute;
    left: 0;
    right: 0;
    bottom: 0;
    height: 22px;
    background: var(--ink-grey);
  }
  .web-tab {
    position: absolute;
    right: 46px;
    bottom: 0;
    min-width: 155px;
    height: 31px;
    padding: 0 14px;
    background: var(--brand-blue);
    border: 1px solid var(--card-white);
    border-bottom: none;
    border-radius: 7px 7px 0 0;
    box-sizing: border-box;
    display: flex;
    align-items: center;
    justify-content: center;
    font-family: "Work Sans", sans-serif;
    font-size: 13px;
    letter-spacing: 0.3px;
    color: var(--card-white);
    white-space: nowrap;
  }
</style>
</head>
<body>
<main class="canvas">

  <section class="card card-front" aria-label="Business card front">
    <div class="brand-name">BRIGHT FERN<br><span class="brand-sub">Mortgage Group</span></div>

    <span class="side-tab"></span>
    <h1 class="person-name">DANIEL MOSS</h1>
    <span class="person-role">CEO</span>
    <span class="role-rule"></span>

    <ul class="contact-list">
      <li>
        <svg viewBox="0 0 10 10" aria-hidden="true"><path d="M2.5 0h5a1 1 0 0 1 1 1v8a1 1 0 0 1-1 1h-5a1 1 0 0 1-1-1V1a1 1 0 0 1 1-1zM3 1.5v6h4v-6z"/></svg>
        000-123-4567
      </li>
      <li>
        <svg viewBox="0 0 10 10" aria-hidden="true"><path d="M2.5 0h5v3h-5zM0 3.5h10v4H8V6H2v1.5H0zM2.5 6.5h5V10h-5z"/></svg>
        000-123-4567
      </li>
      <li>
        <svg viewBox="0 0 10 10" aria-hidden="true"><path d="M0 1.5h10v1L5 5.5 0 2.5zM0 3.7l5 3 5-3V8.5H0z"/></svg>
        daniel.moss@brightfernmg.com
      </li>
    </ul>

    <address class="office-address">Lantern Centre<br>Sydney Melbourne</address>

    <span class="footer-band"></span>
    <div class="web-tab">www.brightfernmg.com</div>
  </section>

  <section class="card card-back" aria-label="Business card back">
    <div class="brand-name">BRIGHT FERN<br><span class="brand-sub">Mortgage Group</span></div>
  </section>

</main>
</body>
</html>
```